Broschüren-Design für Unternehmens- und Personalentwicklung
Zielgruppe
Unternehmens- und Personalentwicklung und bieten Seminare, Workshops und Coachings in den Bereichen Führung/Vertrieb und Persönlichkeitsentwicklung an. Wir arbeiten ausschließlich konzeptionell direkt für Unternehmen. Diese kommen aus den unterschiedlichsten Branchen. Übergeordnet sind es alle Branchen mit unserer Zielgruppe Vorstände, Geschäftsführer, Vertriebleiter und Leitung HR bzw. Personalentwicklung.
Aufgabenstellung
Das Design für unsere Broschüre soll im Wiedererkennungswert zu unserem Impulsgeber (Muster anbei) entstehen. Bestandskunden sollen erkennen, dass es was NEUES, doch aber aus unserem Hause ist. Die Herausforderung für das Projekt ist viel mehr, die Umsetzung von vielen Themen in eine leichte, transparente Gestaltung für eine Druckversion. Die Texte werden dazu geliefert. Die Broschüre beginnt klassisch mit einem Deckblatt - auf der Rückseite, also erste Seite innen die Beschreibung, was wir mit dieser erreichen wollen - die zweite Seite innen, wird mit Profilbildern und einem Claim unserer insgesamt 6 Trainer/innen gestaltet werden. Auf der dann folgenden Seite sind unsere drei Rubriken - Vertrieb, Führung und Potentialwachstum kurz beschrieben. In diesem Rubriken gibt es dann zwischen 11 bis 17 Seminarbeschreibungen - vll geriffelt zum raustrennen?! (Muster auch hier anbei) die dargestellt werden. Wichtig ist, dass der Kunde die Option hat, zunächst in seiner von ihm gewünschten Rubrik die einzelnen Seminarbeschreibungen nachlesen zu können. Am Ende der Broschüre sollte eine Call to Action Option sein, wie zum Beispiel eine Postkarte, wo sich der Kunde mehr Informationen oder ein Beratungsgespräch wünscht. Was wir auf keinen Fall wollen, ist ein klassischer Weiterbildungskatalog wie er von Mitbewerben schon seit gefühlten 25 Jahren produziert wird.
Der Auftrag ist hier also auf der einen Seite die pfiffige Gestaltung der Andersartigkeit - und die Kompetenz einer Druckversion zum Auftrag. Womit wir mit den Daten eine Druckerei finden. Zudem muss der Inhalt der Broschüre bzw. die Darstellung der Seminarthemen und Rubriken auf unserer Homepage verwendet werden.
Da wir an ca. 500 Kunden die Broschüre versenden werden, sind ausser den Druckkosten auch die Versandkosten relevant in der Entscheidung. Also Format sehen wir bisher nur die DIN A4 Version .... sind jedoch sehr offen, für alternative Vorschläge zum Format (Bsp. hier auch un..

```html
<!DOCTYPE html>
<html lang="de">
<head>
<meta charset="utf-8">
<title>kontur – Broschüre Unternehmens- und Personalentwicklung</title>
<link rel="stylesheet" href="https://fonts.googleapis.com/css2?family=Open+Sans:ital,wght@0,400;0,600;0,700;0,800;1,400;1,600;1,800&family=Sorts+Mill+Goudy:ital@0;1&display=swap">
<style>
:root{
  --blue:#0a72bd;
  --blue-dark:#075a99;
  --blue-light:#c6e2f3;
  --orange:#e8622e;
  --text:#6d6d6d;
  --text-dark:#444;
  --paper:#ffffff;
  --backdrop:#e7e7e7;
}
*{box-sizing:border-box;margin:0;padding:0}
html,body{width:1103px;height:1200px;overflow:hidden;background:var(--backdrop)}
.stage{position:absolute;left:0;top:0;width:1848px;height:2011px;transform:scale(.5968);transform-origin:0 0}
.page,.spread{position:absolute;background:var(--paper);overflow:hidden;box-shadow:0 6px 14px rgba(0,0,0,.18)}
.abs{position:absolute}
.serif{font-family:"Sorts Mill Goudy",serif}

/* cover */
.cover{left:924px;top:222px;width:702px;height:496px}
.brand{left:48px;top:40px;font-family:"Open Sans",sans-serif;font-weight:400;font-size:50px;line-height:56px;color:var(--blue)}
.brand-tag{left:50px;top:99px;font-family:"Sorts Mill Goudy",serif;font-size:8px;color:var(--blue);letter-spacing:.6px}
.cover-title{left:190px;top:262px;font-family:"Open Sans",sans-serif;font-weight:800;font-style:italic;font-size:28px;line-height:33px;color:var(--orange);letter-spacing:.5px}

/* spread 2 */
.spread-team{left:222px;top:762px;width:1404px;height:496px}
.services-photo{left:0;top:0;width:702px;height:496px}
.services-title{left:127px;top:110px;font-size:24px;color:#fff;font-weight:400}
.services-col{top:178px;width:150px;font-family:"Open Sans",sans-serif;font-weight:700;font-size:8.3px;line-height:12.6px;color:#fff;text-align:justify;hyphens:manual}
.services-col p{margin-bottom:12.6px}
.fold{left:702px;top:0;width:1px;height:496px;background:#e4e4e4}
.name-box{left:749px;top:72px;width:151px;height:151px;background:var(--blue)}
.name-box span{position:absolute;left:19px;bottom:20px;font-family:"Open Sans",sans-serif;font-weight:700;font-size:24px;line-height:26px;color:#fff}
.portrait{background:linear-gradient(160deg,#efefef,#bdbdbd)}
.quote{left:936px;top:132px;font-size:23px;line-height:24px;color:var(--orange)}
.quote span{display:block}
.bio{left:813px;top:268px;width:323px;font-family:"Open Sans",sans-serif;font-size:7.6px;line-height:12.6px;color:var(--text);text-align:justify}
.bio p{margin-bottom:12.6px}

/* spread 3 */
.spread-seminar{left:222px;top:1301px;width:1404px;height:496px}
.category-quote{left:46px;top:66px;font-size:22px;line-height:23.5px;color:var(--orange)}
.category-quote span{display:block}
.category-box{left:510px;top:47px;width:149px;height:149px;background:var(--blue)}
.category-box span{position:absolute;right:26px;top:55px;text-align:right;font-family:"Open Sans",sans-serif;font-weight:700;font-size:34px;line-height:36px;color:#fff}
.category-col{top:202px;width:150px;font-family:"Open Sans",sans-serif;font-size:7.6px;line-height:12.6px;color:var(--text);text-align:justify;hyphens:manual}
.category-col p{margin-bottom:12.6px}
.seminar-title{left:790px;top:62px;font-style:italic;font-size:21px;line-height:23px;color:var(--blue);font-weight:400}
.trainer-name{left:1251px;top:182px;font-style:italic;font-size:22px;line-height:22px;color:var(--blue)}
.trainer-rule{left:1248px;top:249px;width:65px;height:2px;background:var(--blue)}
.fact{font-family:"Open Sans",sans-serif;font-style:italic;font-size:8px;line-height:11px;color:var(--blue)}
.fact b{font-weight:700}
.block-head{left:795px;font-family:"Open Sans",sans-serif;font-weight:700;font-size:10.5px;color:var(--blue)}
.block-text{left:795px;width:385px;font-family:"Open Sans",sans-serif;font-size:7.6px;line-height:12.6px;color:var(--text);text-align:justify}
.block-text b{font-weight:700;color:var(--text-dark)}
.bullets{left:795px;list-style:none;font-family:"Open Sans",sans-serif;font-size:7.6px;line-height:15.3px;color:var(--text)}
.bullets li{padding-left:15px;position:relative}
.bullets li::before{content:"";position:absolute;left:1px;top:6px;width:4px;height:4px;background:var(--blue)}
</style>
</head>
<body>
<div class="stage">

  <!-- Cover -->
  <section class="page cover">
    <svg class="abs" width="702" height="496" viewBox="0 0 702 496" role="img" aria-label="Blau getöntes Foto: Menschen in Bewegung auf einer geschwungenen Treppe">
      <defs>
        <linearGradient id="coverPhoto" x1="0" y1="0" x2="1" y2="1">
          <stop offset="0" stop-color="#1c86cf"/>
          <stop offset=".55" stop-color="#0a66ad"/>
          <stop offset="1" stop-color="#1478c2"/>
        </linearGradient>
      </defs>
      <polygon points="379,0 702,0 702,496 293,496" fill="url(#coverPhoto)"/>
    </svg>
    <div class="abs brand">kontur</div>
    <div class="abs brand-tag">WEGE MIT WIRKUNG</div>
    <svg class="abs" style="left:0;top:0" width="702" height="496" aria-hidden="true">
      <polygon points="159,227 201,227 197,245 176,245 150,379 172,379 168,397 121,397" fill="var(--blue)"/>
      <polygon points="453,227 494,227 466,397 415,397 419,379 441,379 467,245 449,245" fill="#fff"/>
    </svg>
    <div class="abs cover-title">UNTERNEHMENS-<br>&nbsp;UND PERSONAL-<br>ENTWICKLUNG.</div>
  </section>

  <!-- Spread: Leistungen / Trainer -->
  <section class="spread spread-team">
    <svg class="abs services-photo" width="702" height="496" role="img" aria-label="Blau getöntes Foto: Hochhausfassade von unten mit Flugzeug am Himmel">
      <defs>
        <linearGradient id="servicesPhoto" x1="0" y1="0" x2="1" y2="1">
          <stop offset="0" stop-color="#0a72bd"/>
          <stop offset=".6" stop-color="#1682cc"/>
          <stop offset="1" stop-color="#0b5d9e"/>
        </linearGradient>
      </defs>
      <rect width="702" height="496" fill="url(#servicesPhoto)"/>
    </svg>
    <h2 class="abs serif services-title">Unsere Leistungen</h2>
    <div class="abs services-col" style="left:192px">
      <p>Ob Beratung, Training, Coaching oder … uns geht es immer um kenn ich – hin zum kann ich!</p>
      <p>Aus diesem Grund erleben alle Teil&shy;nehmer das, was wirklich zählt: Di&shy;rekte und unmittel&shy;bare Umset&shy;zung in der Praxis. Wir verbinden neues kogni&shy;tives Wissen mit dem Bewusst&shy;sein hin zu einer automati&shy;sierten Kompe&shy;tenz in eigenen Wegen. Nur dies gewähr&shy;leistet einen direkten Einsatz im Alltag. Und damit den Profit jedes Einzelnen.</p>
      <p>Wir beheben die Ursachen, schaffen</p>
    </div>
    <div class="abs services-col" style="left:351px">
      <p>neue Auswir&shy;kungen und damit ver&shy;änderte Verhaltens&shy;kompe&shy;tenzen. So werden aus alt einge&shy;sessenen Re&shy;aktionen neue Aktions&shy;muster. Raus aus der Box – raus aus der Komfort&shy;zone.</p>
      <p>Über 20 Jahre messbarer und nach&shy;haltiger Erfolg für uns mit unseren Kunden. Klar, transparent und an der Errei&shy;chung der Ziele gemessen. National und inter&shy;national mehr&shy;fach dafür ausge&shy;zeichnet und, noch viel wichtiger, bestätigt durch unse&shy;re Kunden. Konzept mit Wirkung und Wachstum.</p>
    </div>
    <div class="abs fold"></div>

    <div class="abs name-box"><span>JONAS<br>WEHRLE</span></div>
    <div class="abs portrait" style="left:846px;top:46px;width:98px;height:98px" role="img" aria-label="Porträtfoto Trainer Jonas Wehrle"></div>
    <svg class="abs" style="left:919px;top:33px" width="54" height="28" aria-hidden="true">
      <polygon points="10,0 24,0 14,28 0,28" fill="var(--orange)"/>
      <polygon points="38,0 52,0 42,28 28,28" fill="var(--orange)"/>
    </svg>
    <blockquote class="abs serif quote">
      <span style="padding-left:58px">Wer Andere</span>
      <span style="padding-left:92px">kennt ist klug;</span>
      <span>wer sich selbst</span>
      <span style="padding-left:30px">kennt, ist weise.</span>
    </blockquote>
    <div class="abs bio">
      <p>Nosce te ipsum. Erkenne Dich selbst… Ohne eine präsente Wahrnehmung des Gegen&shy;übers und meines Selbst ist alles Gelernte nur ein mechanischer Versuch, mich richtig zu verhalten. Hier liegt ein Schwerpunkt meiner Arbeit mit meinen Trainings&shy;teilnehmern und Coaches. Wer präsent ist, hat in jeder Situation die richtige Handlungs&shy;option. Wenn dies gelingt, ist eine nachhaltige Veränderung möglich.</p>
      <p>„Ich respektiere die Menschen in ihrer Einzigartigkeit. Sie in ihren Veränderungs&shy;prozessen zu begleiten und dabei niemals auszulernen – das ist mein Leben geworden.“</p>
      <p>Gleichzeitig ist es mir wichtig, in meinen Trainings durch Spaß und Erleben eine hohe Aufmerksamkeit zu erzeugen. Es gibt nichts Spannenderes, als den Menschen und dies treibt mich immer wieder an, jeden Teilnehmer individuell wahrzunehmen und ihm das Richtige zu geben. Dann ist er in der Lage, es ab sofort ein wenig anders zu machen…</p>
    </div>
    <div class="abs portrait" style="left:1276px;top:91px;width:81px;height:81px" role="img" aria-label="Porträtfoto Trainer"></div>
    <div class="abs portrait" style="left:1276px;top:184px;width:81px;height:81px" role="img" aria-label="Porträtfoto Trainer"></div>
    <div class="abs portrait" style="left:1276px;top:276px;width:81px;height:81px" role="img" aria-label="Porträtfoto Trainer"></div>
    <div class="abs portrait" style="left:1276px;top:369px;width:81px;height:81px" role="img" aria-label="Porträtfoto Trainer"></div>
  </section>

  <!-- Spread: Rubrik Vertrieb / Seminar -->
  <section class="spread spread-seminar">
    <blockquote class="abs serif category-quote">
      <span style="padding-left:30px">Mus explabo</span>
      <span>repedipiet entusap minis</span>
      <span style="padding-left:42px">maiore&nbsp; more corepe di</span>
      <span style="padding-left:30px">este nullectur.</span>
    </blockquote>
    <div class="abs category-box"><span>VER<br>TRIEB</span></div>
    <div class="abs category-col" style="left:119px">
      <p>Nosce te ipsum. Erkenne Dich selbst… Ohne eine präsente Wahrnehmung des Gegen&shy;übers und meines Selbst ist alles Gelernte nur ein mecha&shy;nischer Versuch, mich richtig zu verhalten. Hier liegt ein Schwer&shy;punkt meiner Arbeit mit meinen Trainings&shy;teil&shy;nehmern und Coaches. Wer präsent ist, hat in jeder Situation die richtige Handlungs&shy;option. Wenn dies gelingt, ist eine nach&shy;haltige Verände&shy;rung möglich.</p>
      <p>„Ich respektiere die Menschen in ihrer Einzig&shy;artigkeit. Sie in ihren Verände&shy;rungs&shy;prozessen zu begleiten und dabei niemals auszulernen – das ist mein Le&shy;ben geworden.“</p>
    </div>
    <div class="abs category-col" style="left:278px">
      <p>Gleichzeitig ist es mir wichtig, in mei&shy;nen Trainings durch Spaß und Erleben eine hohe Aufmerk&shy;samkeit zu erzeugen. Es gibt nichts Spannen&shy;deres, als den Menschen und dies treibt mich immer wieder an, jeden Teilnehmer individuell wahrzu&shy;nehmen und ihm das Richtige zu geben. Dann ist er in der Lage, es ab so&shy;fort ein wenig anders zu machen…</p>
      <p>„Ich respektiere die Menschen in ihrer Einzig&shy;artigkeit. Sie in ihren Verände&shy;rungs&shy;prozessen zu begleiten und dabei niemals auszulernen – das ist mein Le&shy;ben geworden.“</p>
    </div>
    <div class="abs fold"></div>

    <svg class="abs" style="left:0;top:0" width="1404" height="496" aria-hidden="true">
      <polygon points="1253,0 1404,0 1404,496 1168,496" fill="var(--blue-light)"/>
      <polygon points="759,47 787,47 785,56 769,56 761,117 776,117 774,126 750,126" fill="var(--blue)"/>
      <polygon points="961,47 983,47 976,126 950,126 951,117 966,117 973,56 960,56" fill="var(--blue)"/>
    </svg>
    <h3 class="abs serif seminar-title">&nbsp;Seminar<br>Vertriebskompass</h3>
    <div class="abs portrait" style="left:1213px;top:49px;width:96px;height:96px;border:2px solid #fff" role="img" aria-label="Porträtfoto Trainer Malte Brenner"></div>
    <div class="abs serif trainer-name">&nbsp;Malte<br>Brenner</div>
    <div class="abs trainer-rule"></div>
    <div class="abs fact" style="left:1243px;top:272px"><b>Dauer:</b><br>2 Tage</div>
    <div class="abs fact" style="left:1234px;top:312px"><b>Zielgruppe</b><br>Mitarbeiter/innen im Vertrieb</div>
    <div class="abs fact" style="left:1227px;top:357px"><b>Voraussetzung:</b><br>Es gibt keine Voraussetzungen</div>

    <svg class="abs" style="left:748px;top:172px" width="32" height="30" aria-hidden="true">
      <path d="M4 26 L6 19 L24 3 L28 7 L10 23 Z M6 19 L10 23" fill="none" stroke="var(--orange)" stroke-width="1.4"/>
    </svg>
    <div class="abs block-head" style="top:176px">Seminartitel</div>
    <div class="abs block-text" style="top:191px"><b>Gesprächsführung – wer fragt, der führt</b><br>Ursache Nummer 1 ist die Tatsache, dass Bedarfe nicht berücksichtigt sind. Und wer die Kunst der Ermittlung nicht beherrscht, kann und wird es im Angebot nicht widerspiegeln. Fragen der verführen und damit den Kunden dort hin-führen, dass ihre Produkte und Dienstleistungen von ihm gekauft werden. Wer sind Sie – der Kutscher oder das Pferd?!</div>

    <svg class="abs" style="left:749px;top:280px" width="28" height="18" aria-hidden="true">
      <g stroke="var(--orange)" stroke-width="1.2"><line x1="0" y1="2" x2="26" y2="2"/><line x1="0" y1="7" x2="26" y2="7"/><line x1="0" y1="12" x2="26" y2="12"/><line x1="0" y1="17" x2="18" y2="17"/></g>
    </svg>
    <div class="abs block-head" style="top:279px">Inhalte</div>
    <ul class="abs bullets" style="top:296px">
      <li>Fragentechniken, Arten und ihr Mehrwert</li>
      <li>Fragen die zur Veränderung führen</li>
      <li>Grob, Detail- und Bedingungsermittlung</li>
      <li>Fragenkatalog im Arbeitskontext</li>
    </ul>

    <svg class="abs" style="left:749px;top:374px" width="30" height="20" aria-hidden="true">
      <g fill="none" stroke="var(--orange)" stroke-width="1.3"><rect x="1" y="10" width="7" height="8"/><rect x="11" y="6" width="7" height="12"/><rect x="21" y="1" width="7" height="17"/></g>
    </svg>
    <div class="abs block-head" style="top:377px">Mehrwerte für Teilnehmer’innen</div>
    <ul class="abs bullets" style="top:393px">
      <li>Gelassene und souveräne Gesprächsführung</li>
      <li>Fragen für die Anwendung in der Praxis</li>
      <li>Fragen – vom kenn ich zum kann ich</li>
      <li>Fragen die zum Abschluss führen</li>
    </ul>
  </section>

</div>
</body>
</html>
```